Luxury Japanese Matcha Green Tea Packaging Full Packet Design

We're looking for a quality full pack design (front and back) for Ceremonial Grade and Premium Grade Matcha to sell on Bazaarly. We need a 2D versions of front and back images in photoshop and JPG. We also need a 3D versions of front and back for marketing purposes.

You can see our current styling and pack at www.brewvantis.co.uk. However, we want to improve the design and go more professional, simple and elegant with the brand. The last design was from 3 years a go. But hopefully you can see what we are about.

The design will be identical both both packs:

Pack 1: 230mm x 140mm - Premium Grade
Pack 2: 170mm x 120mm - Ceremonial Grade

The design needs to fit both sizes, with pack 1 saying Premium Grade and pack 2 saying Ceremonial Grade.

As many colours as needed, printing is CMYK + White digital printed.

Front of pack:

Product Headline:

Organic Handpicked
Stoneground Japanese Matcha
Green Tea Powder

抹茶

Text: Premium Grade (pack 1) / Ceremonial Grade (pack 2)

100g (pack 1) / 40g (pack 2)

(EU Organic logo)

Back of pack:

Organic Certified GB-ORG-19
Stone Ground Ceremonial Grade Matcha from Uji

Ingredients: 100% Organic Matcha Green Tea Powder

Place of origin: Japan, Store in a cool, dry, dark place
Keep sealed at all times, Best Before 31/03/2020
Not recommended for use if pregnant or nursing

Your next order is ready for you at www.KelpHour.co.uk

Preparing Traditional Matcha Tea:
Sift 1-2g or 1/2 teaspoon of Matcha Green Tea
powder into a bowl or large cup. Add 1/2 cup of hot water
at drinking temperature. Whisk with Bamboo or
Electric Whisk until frothy. Drink immediately.

Preparing Matcha Latte:
Sift 1-2g of Matcha Power into a cup, mix in 2-3 tablespoons of hot water.
Add hot milk and sweetener if desired. Whisk thoroughly.

Nutritional Information:

Per 1g Per 100g
Energy 14.44kJ 1446kJ
3.44kCal 345kCal
Fat 0.04g 4g
Saturates <0.01g 0.6g
Carbohydrates 0.76g 76g
of which sugars 0.47g 47.2g
Protein 0.144g 14.5g
Salt <0.01g 126mg

Per 1g Per 100g
Calcium 1.88mg 191mg
Potassium 94.8mg 3750mg
Iron <0.1g 1.6mg
Zinc <0.1g 1.72mg
Vitamin A 120µg (15% RDA) 2400µg (150% RDA)
Vitamin C 3mg (4% RDA) 60mg (75% RDA)
Folic acid 6µg (6% RDA) 60µg (30% RDA)
Riboflavin 0.1mg (4% RDA) 1.4mg (96% RDA)
Caffeine 17mg 1700mg

Quillon Harbour Ltd. T/A Brewvantis
Company Number: 05617429
Registered Office: 7 The Yard, Darnwick Cl
Newbury, Berkshire, RG17 2QH
social@brewvantis.co.uk
Local Call +44 (0) 20 3184 6057 / Freephone +44 (0) 800 512 7736

This supplement should not be used as a substitute for a varied diet Do not exceed the recommended daily dose.

For more information on Matcha, download the free eBook at www.TheLeafPrimer.com

Please consult a healthcare practitioner if you are pregnant or taking prescription medicine before using this product.

Recommended daily dose

1-5g daily

Storage information: Store in a cool dry place away from sunlight, moisture, and heat. Keep contents dry.

Logos for back of pack:
EU Organic logo with 'GB-ORG-19 Non-EU Agriculture' written directly underneath it.
Vegan logo
Natural Crop Alliance logo
Bazaarly Barcode

Additional deisgn notes:

We have included a design that we like.

The top 2cm will be torn off by the user, so should not contain any key information.

Target Market(s)

High End health and wellness Consumers

Colors
acd036
0455a3
edf8f6

Requirements
Must have
• Stand out on Bazaarly. Show the product to be premium.

```html
<!DOCTYPE html>
<html lang="en">
<head>
<meta charset="utf-8">
<title>Brewvantis Matcha – Back of Pack</title>
<link href="https://fonts.googleapis.com/css2?family=Comfortaa:wght@400;700&family=Roboto+Condensed:wght@400&display=swap" rel="stylesheet">
<style>
  :root {
    --blue: #0455a3;
    --green: #acd036;
    --mint: #edf8f6;
    --navy: #0a2f66;
    --white: #ffffff;
    --ink: #222222;
    --pale-text: #e8f3c4;
  }
  * { margin: 0; padding: 0; box-sizing: border-box; }
  html, body { width: 730px; height: 1200px; overflow: hidden; background: var(--white); }
  body { font-family: 'Comfortaa', sans-serif; color: var(--blue); }
  .pack-back { position: relative; width: 730px; height: 1200px; overflow: hidden; }
  .backdrop { position: absolute; inset: 0; }
  .block { position: absolute; font-size: 12px; line-height: 15.6px; }
  .block strong { font-weight: 700; }
  .cert-line { left: 78px; top: 262px; }
  .product-title { left: 78px; top: 279px; font-size: 18.6px; line-height: 26px; font-weight: 400; white-space: nowrap; }
  .product-title strong { font-weight: 700; }
  .ingredients { left: 78px; top: 342px; }
  .origin { left: 78px; top: 389px; }
  .reorder-bar { position: absolute; left: 0; top: 513px; width: 354px; height: 36px; background: var(--blue); }
  .reorder-bar p { position: absolute; left: 78px; top: 3px; font-size: 12px; line-height: 15.6px; color: var(--white); }
  .prep-tea { left: 78px; top: 584px; width: 290px; }
  .prep-latte { left: 78px; top: 692px; width: 290px; }
  .company { left: 78px; top: 786px; }
  .nutrition-heading { left: 382px; top: 342px; font-weight: 700; }
  .nutrition { position: absolute; left: 382px; top: 360px; border-collapse: separate; border-spacing: 2px 0; font-size: 8.6px; }
  .nutrition th { background: var(--blue); color: var(--white); font-weight: 400; height: 16px; text-align: center; }
  .nutrition th.blank { background: none; }
  .nutrition td { background: var(--mint); height: 17px; border-top: 1px solid var(--white); }
  .nutrition td:first-child { width: 78px; padding-left: 2px; }
  .nutrition td:nth-child(2) { width: 84px; text-align: center; }
  .nutrition td:nth-child(3) { width: 99px; text-align: center; }
  .listing-label { position: absolute; left: 392px; top: 764px; font-family: 'Roboto Condensed', sans-serif; font-size: 9px; line-height: 11px; color: var(--ink); }
  .listing-label .condition { font-size: 10px; }
  .badge-vegan { position: absolute; left: 382px; top: 834px; width: 60px; height: 60px; border-radius: 50%; background: var(--white); border: 3px solid var(--green); }
  .badge-alliance { position: absolute; left: 456px; top: 836px; width: 38px; height: 56px; border-radius: 6px; background: #1d8a3c; }
  .badge-eu { position: absolute; left: 512px; top: 834px; width: 82px; height: 54px; background: #8ab833; }
  .eu-caption { left: 513px; top: 891px; font-size: 8.8px; line-height: 11px; color: var(--ink); }
  .footer-left, .footer-right { color: var(--pale-text); }
  .footer-left { left: 78px; top: 984px; }
  .footer-left p, .footer-right p { margin-bottom: 15.6px; }
  .footer-right { left: 478px; top: 1030px; }
  .footer-right strong { color: var(--white); }
</style>
</head>
<body>
<main class="pack-back">
  <svg class="backdrop" width="730" height="1200" viewBox="0 0 730 1200">
    <polygon points="0,0 730,0 730,250 0,132" fill="var(--blue)"/>
    <polygon points="0,922 730,1006 730,1200 0,1200" fill="var(--green)"/>
    <g role="img" aria-label="Line illustration of camellia blossoms, tea leaves and a matcha bowl along the top left">
      <circle cx="0" cy="140" r="72" fill="var(--green)" stroke="var(--navy)" stroke-width="2"/>
      <ellipse cx="200" cy="20" rx="130" ry="34" fill="#1a4f95"/>
      <ellipse cx="40" cy="230" rx="36" ry="26" fill="#eef2f6"/>
    </g>
    <g role="img" aria-label="Line illustration of a Japanese teapot and bamboo mat in the top right corner">
      <ellipse cx="640" cy="55" rx="100" ry="70" fill="#0c4a90"/>
    </g>
    <g role="img" aria-label="Illustration of a matcha bowl seen from above">
      <circle cx="700" cy="292" r="84" fill="var(--white)" stroke="var(--navy)" stroke-width="1.5"/>
      <circle cx="700" cy="292" r="68" fill="var(--green)"/>
    </g>
  </svg>

  <p class="block cert-line">Organic Certified GB-ORG-19</p>
  <h1 class="block product-title">Stone Ground Ceremonial Grade <strong>Matcha</strong> from Uji</h1>

  <p class="block ingredients"><strong>Ingredients:</strong><br>100% Organic Matcha Green Tea Powder</p>
  <p class="block origin"><strong>Place of origin:</strong> Japan,<br>Store in a cool, dry, dark place<br>Keep sealed at all times<br>Best Before 31/03/2020<br>Not recommended for use<br>if pregnant or nursing</p>

  <div class="reorder-bar"><p>Your next order is ready for<br>you at www.KelpHour.co.uk</p></div>

  <p class="block prep-tea"><strong>Preparing Traditional Matcha Tea:</strong><br>Sift 1-2g or 1/2 teaspoon of Matcha Green Tea powder into a bowl or large cup. Add 1/2 cup of hot water at drinking temperature. Whisk with Bamboo or Electric Whisk until frothy. Drink immediately.</p>
  <p class="block prep-latte"><strong>Preparing Matcha Latte:</strong><br>Sift 1-2g of Matcha Power into a cup, mix in 2-3 tablespoons of hot water. Add hot milk and sweetener if desired. Whisk thoroughly.</p>

  <p class="block company">Quillon Harbour Ltd. T/A Brewvantis<br>Company Number: 05617429<br>Registered Office: 7 The Yard, Darnwick Cl<br>Newbury, Berkshire, RG17 2QH<br>social@brewvantis.co.uk<br>Local Call +44 (0) 20 3184 6057 / Freephone<br>+44 (0) 800 512 7736</p>

  <p class="block nutrition-heading">Nutritional Information:</p>
  <table class="nutrition">
    <thead><tr><th class="blank"></th><th>Per 1g</th><th>Per 100g</th></tr></thead>
    <tbody>
      <tr><td>Energy</td><td>14.44kJ</td><td>1446kJ</td></tr>
      <tr><td></td><td>3.44kCal</td><td>345kCal</td></tr>
      <tr><td>Fat</td><td>0.04g</td><td>4g</td></tr>
      <tr><td>Saturates</td><td>&lt;0.01g</td><td>0.6g</td></tr>
      <tr><td>Carbohydrates</td><td>0.76g</td><td>76g</td></tr>
      <tr><td>of which sugars</td><td>0.47g</td><td>47.2g</td></tr>
      <tr><td>Protein</td><td>0.144g</td><td>14.5g</td></tr>
      <tr><td>Salt</td><td>&lt;0.01g</td><td>126mg</td></tr>
      <tr><td>Calcium</td><td>1.88mg</td><td>191mg</td></tr>
      <tr><td>Potassium</td><td>94.8mg</td><td>3750mg</td></tr>
      <tr><td>Iron</td><td>&lt;0.1g</td><td>1.6mg</td></tr>
      <tr><td>Zinc</td><td>&lt;0.1g</td><td>1.72mg</td></tr>
      <tr><td>Vitamin A</td><td>120µg (15% RDA)</td><td>2400µg (150% RDA)</td></tr>
      <tr><td>Vitamin C</td><td>3mg (4% RDA)</td><td>60mg (75% RDA)</td></tr>
      <tr><td>Folic acid</td><td>6µg (6% RDA)</td><td>60µg (30% RDA)</td></tr>
      <tr><td>Riboflavin</td><td>0.1mg (4% RDA)</td><td>1.4mg (96% RDA)</td></tr>
      <tr><td>Caffeine</td><td>17mg</td><td>1700mg</td></tr>
    </tbody>
  </table>

  <p class="listing-label">Matcha Green Tea Pow...ty, Vegan and non-GMO<br><span class="condition">New</span></p>

  <div class="badge-vegan" role="img" aria-label="Vegan certification badge"></div>
  <div class="badge-alliance" role="img" aria-label="Natural Crop Alliance certified organic badge"></div>
  <div class="badge-eu" role="img" aria-label="EU organic certification badge"></div>
  <p class="block eu-caption">GB-ORG-19<br>Non-EU Agriculture</p>

  <div class="block footer-left">
    <p>This supplement should not be<br>used as a substitute for a varied diet</p>
    <p>Do not exceed the recommended daily dose.</p>
    <p>For more information on Matcha, download the<br>free eBook at www.TheLeafPrimer.com</p>
    <p>Please consult a healthcare practitioner if you are pregnant<br>or taking prescription medicine before using this product.</p>
  </div>
  <div class="block footer-right">
    <p>Recommended daily dose<br><strong>1-5g daily</strong></p>
    <p><strong>Storage information:</strong><br>Store in a cool dry place<br>away from sunlight, moisture,<br>and heat. Keep contents dry.</p>
  </div>
</main>
</body>
</html>
```